Android App Design Project

Hi my name is Nadir, and I'm an android developer. I'm searching for a professional designer that can design my app.I have already launched the app and you can find it in the apptrove bazaar.

Main Requirements
- 15 sport icons
- 6 android pages
- Action bar
- Buttons and other icons

You need to do all requirements to submit a design. I need the design in both JPEG format and Photoshop PSD format. If you are interested then please download the PDF file ,it will help you a lot.
The name of the app is "MATCH VIEW Classic" you can find it in Orbix Shelf.

NOTICE: You might read that the Payment is not guaranteed if I'm not happy with the design BUT if you make a good design and you win the contest, then you become my main designer that means if I want to change or add something to the design of the app in the future I return to you "the winner" directly to make the redesign and get paid for it.

Regards.
Skype: Fadi Hamoudi "fadi48"
E-mail: fadinadir@quillpost.net

Industry/Entity Type

Tv

Requirements
Must have
• - 15 sport icons
- 6 android pages
- Action bar
- Buttons and other icons

```html
<!DOCTYPE html>
<html lang="en">
<head>
<meta charset="UTF-8">
<title>Live update</title>
<link rel="stylesheet" href="https://fonts.googleapis.com/css2?family=Roboto+Condensed:wght@400;700&display=swap">
<style>
  :root {
    --bar-top: #f5873a;
    --bar-bottom: #e2621c;
    --bar-edge: #b84a10;
    --screen-bg: #232323;
    --row-line: #4a4a4a;
    --row-shadow: #141414;
    --text-main: #ffffff;
    --text-accent: #f28a2e;
    --live-on: #57d62a;
    --live-on-dark: #2e8a12;
    --live-off: #d9d9d9;
    --live-off-dark: #8a8a8a;
    --back-face: #fbeee4;
  }
  html, body {
    margin: 0;
    padding: 0;
    overflow: hidden;
    background: var(--screen-bg);
  }
  .screen {
    width: 817px;
    height: 1200px;
    overflow: hidden;
    position: relative;
    background: radial-gradient(ellipse at 50% 40%, #2b2b2b 0%, var(--screen-bg) 70%);
    font-family: "Roboto Condensed", "Arial Narrow", sans-serif;
    color: var(--text-main);
  }
  .action-bar {
    height: 102px;
    position: relative;
    background: linear-gradient(to bottom, var(--bar-top), var(--bar-bottom));
    border-bottom: 2px solid var(--bar-edge);
    box-sizing: border-box;
    display: flex;
    align-items: center;
    justify-content: center;
  }
  .action-bar__title {
    font-size: 40px;
    font-weight: 400;
    letter-spacing: 0.5px;
    text-shadow: 0 1px 2px rgba(0,0,0,0.25);
  }
  .back-button {
    position: absolute;
    left: 20px;
    top: 26px;
    width: 77px;
    height: 50px;
    border-radius: 10px;
    background: linear-gradient(to bottom, #ffffff, var(--back-face));
    box-shadow: inset 0 -2px 3px rgba(0,0,0,0.15), 0 1px 2px rgba(0,0,0,0.3);
    display: flex;
    align-items: center;
    justify-content: center;
  }
  .match-list {
    list-style: none;
    margin: 0;
    padding: 0;
  }
  .match-row {
    height: 137px;
    box-sizing: border-box;
    border-bottom: 2px solid var(--row-line);
    box-shadow: inset 0 -3px 0 var(--row-shadow);
    position: relative;
    padding: 44px 0 0 20px;
  }
  .match-row--inset { padding-left: 28px; }
  .match-time, .match-teams {
    font-size: 31px;
    line-height: 33px;
    margin: 0;
  }
  .match-time__value, .match-teams__vs { color: var(--text-accent); }
  .match-time__value { margin-left: 12px; }
  .live-dot {
    position: absolute;
    right: 31px;
    top: 55px;
    width: 30px;
    height: 30px;
    border-radius: 50%;
  }
  .live-dot--on {
    background: radial-gradient(circle at 40% 35%, #b8ff8a 0%, var(--live-on) 40%, var(--live-on-dark) 100%);
    box-shadow: 0 0 10px rgba(87,214,42,0.6);
  }
  .live-dot--off {
    background: radial-gradient(circle at 40% 35%, #ffffff 0%, var(--live-off) 45%, var(--live-off-dark) 100%);
    box-shadow: 0 1px 2px rgba(0,0,0,0.6);
  }
</style>
</head>
<body>
<div class="screen">
  <header class="action-bar">
    <div class="back-button" aria-label="Back">
      <svg width="40" height="28" viewBox="0 0 40 28">
        <path d="M2 14 L16 2 L16 9 L38 9 L38 19 L16 19 L16 26 Z" fill="#e8641e"/>
      </svg>
    </div>
    <h1 class="action-bar__title">Live update</h1>
  </header>

  <ul class="match-list">
    <li class="match-row">
      <p class="match-time">Time <span class="match-time__value">21:00</span></p>
      <p class="match-teams">Austrilia <span class="match-teams__vs">vs</span> India</p>
      <span class="live-dot live-dot--on"></span>
    </li>
    <li class="match-row">
      <p class="match-time">Time <span class="match-time__value">21:00</span></p>
      <p class="match-teams">India <span class="match-teams__vs">vs</span> Pakistan</p>
      <span class="live-dot live-dot--off"></span>
    </li>
    <li class="match-row">
      <p class="match-time">Time <span class="match-time__value">21:00</span></p>
      <p class="match-teams">Canada <span class="match-teams__vs">vs</span> China</p>
      <span class="live-dot live-dot--off"></span>
    </li>
    <li class="match-row match-row--inset">
      <p class="match-time">Time <span class="match-time__value">21:00</span></p>
      <p class="match-teams">Austrilia <span class="match-teams__vs">vs</span> India</p>
      <span class="live-dot live-dot--on"></span>
    </li>
    <li class="match-row match-row--inset">
      <p class="match-time">Time <span class="match-time__value">21:00</span></p>
      <p class="match-teams">India <span class="match-teams__vs">vs</span> Pakistan</p>
      <span class="live-dot live-dot--off"></span>
    </li>
    <li class="match-row match-row--inset">
      <p class="match-time">Time <span class="match-time__value">21:00</span></p>
      <p class="match-teams">Canada <span class="match-teams__vs">vs</span> China</p>
      <span class="live-dot live-dot--on"></span>
    </li>
    <li class="match-row match-row--inset">
      <p class="match-time">Time <span class="match-time__value">21:00</span></p>
      <p class="match-teams">Austrilia <span class="match-teams__vs">vs</span> India</p>
      <span class="live-dot live-dot--on"></span>
    </li>
    <li class="match-row match-row--inset">
      <p class="match-time">Time <span class="match-time__value">21:00</span></p>
      <p class="match-teams">Canada <span class="match-teams__vs">vs</span> China</p>
      <span class="live-dot live-dot--off"></span>
    </li>
  </ul>
</div>
</body>
</html>
```